Harborline Auto LLC

Car Dealer Customer Service
Address: 2874 Cresthaven Road, Alderwick, ND 58999
web: www.harborlineautoxq.net
email: harborlineautoxq@mailnest.example
Phone: (555) 555-0148
Phone: (555) 555-0173

```html
<!DOCTYPE html>
<html lang="en">
<head>
<meta charset="utf-8">
<title>Harborline Auto LLC – Business Card</title>
<link rel="stylesheet" href="https://fonts.googleapis.com/css2?family=Montserrat:wght@600;700&family=Roboto:wght@400;500&display=swap">
<style>
  :root {
    --backdrop: #3a3a3a;
    --card: #1a1a1a;
    --edge-blue: #1f8fd6;
    --brand-blue: #2a8fd1;
    --accent-gold: #f2b234;
    --text-light: #ececec;
    --pattern-dark: #121212;
    --pattern-mid: #262626;
  }
  * { box-sizing: border-box; margin: 0; padding: 0; }
  html, body { width: 1200px; height: 801px; overflow: hidden; }
  body {
    background: var(--backdrop);
    font-family: "Roboto", Arial, sans-serif;
    position: relative;
  }
  .card {
    position: absolute;
    top: 246px;
    width: 540px;
    height: 309px;
    background: var(--card);
    border-bottom: 4px solid var(--edge-blue);
    box-shadow: 0 10px 30px rgba(0,0,0,.45);
    overflow: hidden;
  }
  .card--front { left: 40px; }
  .card--back { left: 620px; }

  .brand {
    position: absolute;
    top: 46px; left: 0; right: 0;
    display: flex; align-items: center; justify-content: center; gap: 12px;
  }
  .brand__dot {
    flex: none;
    width: 34px; height: 34px; border-radius: 50%;
    background: var(--brand-blue);
  }
  .brand__name {
    font-family: "Montserrat", Arial, sans-serif;
    font-weight: 700;
    font-size: 30px;
    letter-spacing: .5px;
    color: var(--brand-blue);
    white-space: nowrap;
  }
  .tagline {
    position: absolute;
    top: 124px; left: 28px; right: 28px;
    display: flex; align-items: center; gap: 12px;
  }
  .tagline__rule { flex: 1; height: 1.5px; background: var(--accent-gold); }
  .tagline__text {
    font-family: "Montserrat", Arial, sans-serif;
    font-weight: 700;
    font-size: 15px;
    color: var(--brand-blue);
    letter-spacing: .3px;
    white-space: nowrap;
  }
  .contacts {
    position: absolute;
    left: 34px; bottom: 40px;
    list-style: none;
    font-size: 14px;
    color: var(--text-light);
    line-height: 22px;
  }
  .contacts li { display: flex; align-items: center; gap: 8px; white-space: nowrap; }
  .contacts svg { width: 12px; height: 12px; fill: var(--accent-gold); flex: none; }
  .location {
    position: absolute;
    right: 34px; bottom: 40px;
    text-align: right;
    font-size: 14px;
    font-style: normal;
    line-height: 22px;
    color: var(--text-light);
    white-space: nowrap;
  }
  .location__web { color: var(--accent-gold); font-weight: 500; }

  .pattern {
    position: absolute; inset: 0;
    background: linear-gradient(135deg, var(--pattern-dark) 0%, var(--pattern-mid) 55%, var(--pattern-dark) 100%);
  }
  .back-brand {
    position: absolute;
    top: 50%; left: 50%;
    transform: translate(-50%, -50%);
    display: flex; align-items: center; gap: 10px;
    background: var(--card);
    padding: 10px 16px;
  }
  .back-brand .brand__name { font-size: 24px; }
  .back-brand .brand__dot { width: 28px; height: 28px; }
</style>
</head>
<body>

<section class="card card--front" aria-label="Business card front">
  <div class="brand">
    <span class="brand__dot"></span>
    <span class="brand__name">HARBORLINE AUTO</span>
  </div>

  <div class="tagline">
    <span class="tagline__rule"></span>
    <span class="tagline__text">CAR DEALER CUSTOMER SERVICE</span>
    <span class="tagline__rule"></span>
  </div>

  <ul class="contacts">
    <li>
      <svg viewBox="0 0 24 24" aria-hidden="true"><path d="M6.6 10.8a15.1 15.1 0 0 0 6.6 6.6l2.2-2.2a1 1 0 0 1 1-.25 11.4 11.4 0 0 0 3.6.57 1 1 0 0 1 1 1V20a1 1 0 0 1-1 1A17 17 0 0 1 3 4a1 1 0 0 1 1-1h3.5a1 1 0 0 1 1 1c0 1.25.2 2.45.57 3.57a1 1 0 0 1-.25 1z"/></svg>
      (555) 555-0148
    </li>
    <li>
      <svg viewBox="0 0 24 24" aria-hidden="true"><path d="M6.6 10.8a15.1 15.1 0 0 0 6.6 6.6l2.2-2.2a1 1 0 0 1 1-.25 11.4 11.4 0 0 0 3.6.57 1 1 0 0 1 1 1V20a1 1 0 0 1-1 1A17 17 0 0 1 3 4a1 1 0 0 1 1-1h3.5a1 1 0 0 1 1 1c0 1.25.2 2.45.57 3.57a1 1 0 0 1-.25 1z"/></svg>
      (555) 555-0173
    </li>
    <li>
      <svg viewBox="0 0 24 24" aria-hidden="true"><path d="M2 5h20v14H2zm2 2v.5l8 5 8-5V7l-8 5z"/></svg>
      harborlineautoxq@mailnest.example
    </li>
  </ul>

  <address class="location">
    2874 Cresthaven Road<br>
    Alderwick, ND 58999<br>
    <span class="location__web">www.harborlineautoxq.net</span>
  </address>
</section>

<section class="card card--back" aria-label="Business card back">
  <div class="pattern" role="img" aria-label="Repeating embossed pattern of the brand emblem in dark tones"></div>
  <div class="back-brand">
    <span class="brand__dot"></span>
    <span class="brand__name">HARBORLINE AUTO</span>
  </div>
</section>

</body>
</html>
```